I need a new business card designed, we recently rebranded and I need to get a fresh design to match our new logo, colours and branding.

Details:

Derek Havill | Founder & CEO
Address: 7 Marlowfern Lane, #09-14 Tavenport Crest, Singapore 318547
Tel: +65 93568214
Web: www.frostkarta.com.sg
hello@frostkarta.com.sg

I've attached my old card as well

Industry/Entity Type

Business

Requirements
Must have
• Front and Back
Interesting use of logo
Correct use of colour scheme

```html
<!DOCTYPE html>
<html lang="en">
<head>
<meta charset="utf-8">
<title>Frostkarta Business Card – Front and Back</title>
<link rel="stylesheet" href="https://fonts.googleapis.com/css2?family=Source+Sans+3:wght@400;600&family=Arimo:wght@400&display=swap">
<style>
  :root {
    --stage: #000000;
    --card: #ffffff;
    --label: #6e6e6e;
    --ink: #111111;
    --muted: #b9b9b9;
    --brand-ice: #3fb6ea;
    --brand-stone: #8c7c72;
  }
  * { margin: 0; padding: 0; box-sizing: border-box; }
  html, body { width: 1200px; height: 1000px; overflow: hidden; background: var(--stage); }
  .stage { position: relative; width: 1200px; height: 1000px; }

  .side-label {
    position: absolute;
    font-family: "Source Sans 3", sans-serif;
    font-size: 24px;
    color: var(--label);
  }
  .side-label--front { left: 182px; top: 83px; }
  .side-label--back { left: 182px; top: 557px; }

  .card { position: absolute; background: var(--card); }
  .card--front { left: 259px; top: 72px; width: 698px; height: 395px; }
  .card--back { left: 261px; top: 542px; width: 693px; height: 398px; }

  .brand { position: absolute; display: flex; align-items: center; gap: 11px; }
  .brand__dot { width: 62px; height: 62px; border-radius: 50%; background: var(--brand-ice); flex: none; }
  .brand__name {
    font-family: "Source Sans 3", sans-serif;
    font-weight: 600;
    font-size: 40px;
    color: var(--brand-stone);
    line-height: 1;
    letter-spacing: -0.5px;
  }
  .card--front .brand { left: 51px; top: 48px; }
  .card--back .brand { left: 235px; top: 167px; }

  .person {
    position: absolute; left: 51px; top: 174px;
    font-family: "Source Sans 3", sans-serif;
    font-size: 32px; color: var(--ink); white-space: nowrap;
  }
  .person__sep { margin: 0 4px; }
  .person__role { color: var(--muted); }

  .contact {
    position: absolute; left: 51px;
    font-family: Arimo, Arial, sans-serif;
    font-size: 17px; color: var(--ink);
  }
  .contact__row { display: flex; height: 26.5px; align-items: center; white-space: nowrap; }
  .contact__key { width: 86px; }
  .contact__colon { width: 20px; }
  .contact--lines { top: 242px; }
  .contact--address { top: 341px; font-size: 18px; }
</style>
</head>
<body>
<main class="stage">
  <span class="side-label side-label--front">Front</span>
  <section class="card card--front" aria-label="Card front">
    <div class="brand">
      <span class="brand__dot"></span>
      <span class="brand__name">frostkarta</span>
    </div>
    <p class="person">Derek Havill<span class="person__sep">|</span><span class="person__role">Founder &amp; CEO</span></p>
    <div class="contact contact--lines">
      <div class="contact__row"><span class="contact__key">Tel</span><span class="contact__colon">:</span><span>+65 93568214</span></div>
      <div class="contact__row"><span class="contact__key">Web</span><span class="contact__colon">:</span><span>www.frostkarta.com.sg</span></div>
      <div class="contact__row"><span class="contact__key">e-mail</span><span class="contact__colon">:</span><span>hello@frostkarta.com.sg</span></div>
    </div>
    <div class="contact contact--address">
      <div class="contact__row"><span class="contact__key">Address</span><span class="contact__colon">:</span><span>7 Marlowfern Lane, #09-14 Tavenport Crest, Singapore 318547</span></div>
    </div>
  </section>

  <span class="side-label side-label--back">Back</span>
  <section class="card card--back" aria-label="Card back">
    <div class="brand">
      <span class="brand__dot"></span>
      <span class="brand__name">frostkarta</span>
    </div>
  </section>
</main>
</body>
</html>
```